I am looking for a modern, clean and neat design for a reflexology and well being business. The business name is Gralo Tund (this is an old Latin word for wellbeing). The colours I would like are purple, white and grey. I am open to suggestions for pictures such as healing or working hands, a pair of feet, images that represent my business that you may think of....... or maybe you think no images at all would be best? My tag line is: "Relax, Renew, Revive" or "Find you balance......... Relax, Renew, Revive" I can decide which I want so I would like to see what both would look like. I would like space on the back to write the client's appointment date and time (more than once)

```html
<!DOCTYPE html>
<html lang="en">
<head>
<meta charset="utf-8">
<title>Gralo Tund – Business Card</title>
<link href="https://fonts.googleapis.com/css2?family=Roboto:wght@700&family=Open+Sans:wght@400;600&family=Libre+Baskerville&display=swap" rel="stylesheet">
<style>
  :root {
    --backdrop: #151515;
    --card: #ffffff;
    --magenta: #d11ed8;
    --plum: #a02a92;
    --ink: #3c3c3c;
    --ink-dark: #222222;
  }
  * { box-sizing: border-box; margin: 0; padding: 0; }
  html, body { width: 1200px; height: 900px; overflow: hidden; }
  body {
    background: var(--backdrop);
    font-family: "Open Sans", Arial, sans-serif;
    position: relative;
  }
  .card {
    position: absolute;
    top: 306px;
    width: 440px;
    height: 271px;
    background: var(--card);
    border-radius: 12px;
  }
  .card--front { left: 148px; }
  .card--back { left: 608px; }

  /* Front */
  .brand-mark {
    position: absolute; left: 103px; top: 76px;
    width: 54px; height: 54px; border-radius: 50%;
    border: 2px solid var(--ink-dark);
  }
  .brand-name {
    position: absolute; left: 0; width: 260px; top: 136px;
    text-align: center;
    font-family: "Roboto", Arial, sans-serif; font-weight: 700;
    font-size: 40px; line-height: 1; color: var(--magenta);
  }
  .tagline {
    position: absolute; left: 0; width: 260px; top: 182px;
    text-align: center;
    font-family: "Libre Baskerville", "Times New Roman", serif;
    font-size: 11.5px; letter-spacing: 1.8px; color: var(--ink-dark);
  }
  .contact { position: absolute; left: 250px; top: 68px; color: var(--ink); font-size: 12px; line-height: 15px; }
  .contact__name { font-weight: 600; font-size: 15px; color: var(--magenta); line-height: 19px; }
  .contact__role { margin-bottom: 11px; }
  .contact__address { margin-bottom: 13px; }
  .contact__row { display: flex; align-items: center; gap: 7px; height: 16px; }
  .contact__row svg { width: 9px; height: 9px; fill: var(--magenta); flex: none; }

  /* Back */
  .appt { color: var(--plum); }
  .appt__title {
    position: absolute; top: 32px; left: 0; width: 100%;
    text-align: center; font-weight: 600; font-size: 18px;
  }
  .appt__field { position: absolute; left: 54px; font-size: 13px; font-weight: 600; white-space: nowrap; }
  .appt__field .dots { font-weight: 400; letter-spacing: 0.5px; }
  .appt__field .ampm { font-weight: 400; }
  .appt__field--name { top: 80px; }
  .appt__field--date { top: 129px; }
  .days { position: absolute; top: 176px; left: 36px; display: flex; font-size: 12px; color: var(--ink); }
  .day { display: flex; align-items: center; gap: 5px; margin-right: 14px; }
  .day__box { width: 16px; height: 16px; border: 1.5px solid var(--plum); }
  .appt__notice {
    position: absolute; top: 218px; left: 0; width: 100%;
    text-align: center; font-weight: 600; font-size: 13.5px;
  }
</style>
</head>
<body>
  <section class="card card--front">
    <div class="brand-mark"></div>
    <div class="brand-name">Gralo Tund</div>
    <div class="tagline">RELAX, RENEW, REVIVE</div>
    <div class="contact">
      <div class="contact__name">Marcus Hale</div>
      <div class="contact__role">Managing Director</div>
      <div class="contact__address">12345, Address Goes Here<br>Country Name, 123456.</div>
      <div class="contact__row">
        <svg viewBox="0 0 10 10"><path d="M2 0.5 L3.8 2.6 L2.9 3.8 Q4 6 6.2 7.1 L7.4 6.2 L9.5 8 L8.3 9.5 Q4 9.5 0.5 5 Q0.5 2 2 0.5Z"/></svg>
        <span>044-987 654 321</span>
      </div>
      <div class="contact__row">
        <svg viewBox="0 0 10 10"><path d="M0.5 2 H9.5 V8 H0.5Z M0.5 2 L5 5.5 L9.5 2" stroke="#fff" stroke-width="0.8"/></svg>
        <span>hello@gralotund.com</span>
      </div>
      <div class="contact__row">
        <svg viewBox="0 0 10 10"><circle cx="5" cy="5" r="4.5"/><path d="M0.5 5 H9.5 M5 0.5 Q2.5 5 5 9.5 M5 0.5 Q7.5 5 5 9.5" stroke="#fff" stroke-width="0.7" fill="none"/></svg>
        <span>www.gralotund.com</span>
      </div>
    </div>
  </section>

  <section class="card card--back appt">
    <h2 class="appt__title">Your Next Appointment on</h2>
    <div class="appt__field appt__field--name">Name : <span class="dots">...........................................................................</span></div>
    <div class="appt__field appt__field--date">Date : <span class="dots">...............................</span>&nbsp;&nbsp; Time : <span class="dots">............................</span> <span class="ampm">AM / PM</span></div>
    <div class="days">
      <div class="day"><span class="day__box"></span>MON</div>
      <div class="day"><span class="day__box"></span>TUE</div>
      <div class="day"><span class="day__box"></span>WED</div>
      <div class="day"><span class="day__box"></span>THU</div>
      <div class="day"><span class="day__box"></span>FRI</div>
      <div class="day"><span class="day__box"></span>SAT</div>
    </div>
    <p class="appt__notice">If unable to keep appointment,&nbsp; kindly give 24hrs notice.</p>
  </section>
</body>
</html>
```